Business Cards for a law firm

Business cards for our law firm. Use our silhoette logo and OAK PARTNERS - check our website (www.oakpartners.example)

Contact Information for Business Card

our silhouette logo, OAK PARTNERS, 800-555-0147, Dorian Pemberton, dorian@oakpartners.example

Requirements
Must have
• our silhouette logo, OAK PARTNERS, 800-555-0147, Dorian Pemberton, dorian@oakpartners.example

```html
<!DOCTYPE html>
<html lang="en">
<head>
<meta charset="utf-8">
<title>Oak Partners – Business Cards</title>
<link rel="stylesheet" href="https://fonts.googleapis.com/css2?family=Marcellus+SC&family=Arimo:wght@400&display=swap">
<style>
  :root {
    --backdrop: #9a9a9a;
    --paper: #f7f7f6;
    --navy: #182d68;
    --ink: #2a2a2a;
    --white: #ffffff;
  }
  * { box-sizing: border-box; margin: 0; padding: 0; }
  html, body { width: 1200px; height: 1050px; overflow: hidden; }
  body {
    background: var(--backdrop);
    position: relative;
    font-family: "Arimo", Arial, sans-serif;
  }
  .card {
    position: absolute;
    left: 290px;
    width: 620px;
    height: 354px;
    border-radius: 22px;
    box-shadow: 0 6px 18px rgba(0,0,0,0.18);
    overflow: hidden;
  }
  .card--front { top: 150px; background: var(--paper); }
  .card--back  { top: 560px; background: var(--navy); }

  .front-brand {
    position: absolute;
    right: 56px;
    top: 118px;
    display: flex;
    align-items: center;
    gap: 12px;
    font-family: "Marcellus SC", serif;
    font-size: 26px;
    letter-spacing: 0.06em;
    color: var(--navy);
  }
  .front-brand .mark-square {
    width: 22px; height: 22px;
    background: var(--navy);
  }
  .holder-name {
    position: absolute;
    left: 48px;
    top: 232px;
    font-family: "Marcellus SC", serif;
    font-size: 24px;
    letter-spacing: 0.05em;
    color: var(--navy);
  }
  .contact-line {
    position: absolute;
    left: 48px;
    top: 278px;
    font-size: 14px;
    letter-spacing: 0.02em;
    color: var(--ink);
    white-space: nowrap;
  }
  .contact-line .sep { margin: 0 12px; }

  .back-brand {
    position: absolute;
    left: 0; right: 0;
    top: 132px;
    display: flex;
    justify-content: center;
    align-items: center;
    gap: 20px;
    font-family: "Marcellus SC", serif;
    font-size: 46px;
    letter-spacing: 0.08em;
    color: var(--white);
  }
  .back-brand .mark-square {
    width: 38px; height: 38px;
    background: var(--white);
  }
</style>
</head>
<body>
  <section class="card card--front" aria-label="Business card front">
    <div class="front-brand"><span class="mark-square"></span>OAK PARTNERS</div>
    <h1 class="holder-name">Dorian Pemberton</h1>
    <p class="contact-line">
      <span class="phone">800-555-0147</span><span class="sep">|</span><span class="email">dorian@oakpartners.example</span><span class="sep">|</span><span class="web">www.oakpartners.example</span>
    </p>
  </section>

  <section class="card card--back" aria-label="Business card back">
    <div class="back-brand"><span class="mark-square"></span>OAK PARTNERS</div>
  </section>
</body>
</html>
```